Simple, High-Class Web Design Wanted - Motivational Speakers Site

1. Full Brief/Request & Specs outlined on following video -
http://clipvault-demo.com/watch/rTkWmaPzQb

2. Use colours, images as you feel suits objective (we are happy to pay up to US$30 for any good images but must have licence/permission).

3. Layout probably similar to existing site - www.podiumtalentgroup.com.au / http://podiumtalentgroup.com.au/contact.php

4. Must Be Able to Coded for MOBILE-FRIENDLINESS & WordPress friendly Ideal.

5. This is the first, small job of many we/graphic design jobs. If suits, winning designer may be offered all future work direct.

Thanks & look forward to your design. Glen.

Target Market(s)

corporates - high end

Number of Pages Required

2 page

Font styles to use
Sans Serif

Requirements
Must have
• Classy professional look
Nice to have
• all in Video in brief
Should not have
• too many images / new images I haven't approved

```html
<!DOCTYPE html>
<html lang="en">
<head>
<meta charset="utf-8">
<title>Podium Talent Group – Speakers</title>
<link href="https://fonts.googleapis.com/css2?family=Open+Sans:wght@400;600;700&family=Oswald:wght@500;700&display=swap" rel="stylesheet">
<style>
:root{
  --teal:#1a9ba6;
  --teal-dark:#0f6f79;
  --teal-deep:#0b5961;
  --orange:#f3a22b;
  --ink:#333b40;
  --muted:#6b7479;
  --light:#eef3f4;
  --white:#ffffff;
}
*{box-sizing:border-box;margin:0;padding:0}
html,body{width:1200px;height:2840px;overflow:hidden}
body{font-family:'Open Sans',Arial,sans-serif;color:var(--ink);background:var(--white);position:relative}
section,header,nav,footer{position:absolute;left:0;width:1200px}

/* header */
.site-header{top:0;height:220px;text-align:center}
.promo-pill{display:inline-block;margin-top:28px;background:var(--teal);color:var(--white);font-weight:700;font-size:25px;padding:10px 34px;border-radius:30px}
.promo-sub{font-size:24px;margin-top:10px;color:var(--ink)}
.promo-tag{font-size:16px;color:var(--teal);margin-top:12px;line-height:1.45}
.promo-tag b{color:var(--teal-dark)}
.social{position:absolute;right:40px;top:120px;display:flex;gap:8px}
.social span{width:30px;height:30px;background:#c9d6d8;border-radius:4px}

/* nav */
.main-nav{top:220px;height:34px;background:var(--teal);display:flex;align-items:center;padding-left:40px;gap:26px}
.main-nav a{color:var(--white);font-size:13px;font-weight:700;text-decoration:none;letter-spacing:.3px}

/* hero */
.hero{top:254px;height:466px}
.hero-photo{position:absolute;inset:0;background:linear-gradient(90deg,#5b6b73,#a9b2b6 45%,#d8d4ce 70%,#7f7a75)}
.hero-caption{position:absolute;left:0;right:0;top:290px;text-align:center}
.hero-title{display:inline-block;font-family:'Oswald',Arial,sans-serif;font-weight:700;font-size:54px;color:var(--white);background:rgba(20,30,35,.55);padding:2px 26px;letter-spacing:1px}
.hero-sub{color:var(--white);font-size:18px;margin-top:4px}
.hero-btn{display:inline-block;margin-top:14px;background:var(--teal);color:var(--white);font-weight:700;font-size:14px;padding:10px 28px;border-radius:20px}
.hero-arrow{position:absolute;top:220px;width:40px;height:40px;border-radius:50%;background:var(--teal)}
.hero-arrow svg{width:40px;height:40px}

/* featured */
.featured{top:730px;height:440px;text-align:center}
.featured h2{font-size:40px;font-weight:600;color:var(--ink);margin-top:6px}
.carousel-ctrl{display:flex;justify-content:center;gap:16px;margin-top:40px}
.carousel-ctrl span{width:44px;height:44px;border-radius:50%;background:var(--teal);display:block}
.carousel-ctrl svg{width:44px;height:44px}
.speaker-row{position:absolute;top:170px;left:0;width:1200px;height:250px}
.speaker{position:absolute;top:20px;height:220px;background:linear-gradient(180deg,#dfe3e5,#b9c0c4)}
.speaker-card{position:absolute;left:470px;top:0;width:260px;height:250px;background:var(--teal);border:4px solid var(--teal-dark)}
.speaker-card .photo{position:absolute;inset:0;background:linear-gradient(180deg,#3aa9b2,#17808a)}
.speaker-card .name{position:absolute;left:0;right:0;top:158px;font-family:'Oswald',Arial,sans-serif;color:var(--white);font-size:30px;font-weight:500}
.speaker-card .profile{position:absolute;left:70px;top:206px;width:120px;background:var(--teal-deep);color:var(--white);font-size:12px;font-weight:700;padding:6px 0}

/* welcome */
.welcome{top:1180px;height:330px;background:linear-gradient(180deg,var(--teal),var(--teal-dark));color:var(--white);text-align:center}
.welcome h2{font-size:40px;font-weight:700;margin-top:44px}
.welcome p{font-size:14px;line-height:1.6;width:1100px;margin:26px auto 0;text-align:left}
.form-btn{display:inline-block;margin-top:28px;background:var(--white);color:var(--orange);font-weight:700;font-size:15px;padding:12px 40px;border-radius:24px}

/* video */
.video{top:1510px;height:460px;background:linear-gradient(180deg,#e6eced,#ffffff)}
.player{position:absolute;left:145px;top:16px;width:910px;height:330px;background:#1d2226;border-radius:22px;overflow:hidden}
.play{position:absolute;left:430px;top:120px;width:54px;height:54px;background:var(--teal);border-radius:6px}
.play svg{width:54px;height:54px}
.play-label{position:absolute;left:0;right:0;top:190px;text-align:center;color:var(--white);font-weight:700;font-size:18px}
.player-bar{position:absolute;left:0;right:0;bottom:0;height:30px;background:#2b3136;display:flex;align-items:center;padding:0 16px;gap:12px}
.player-bar .track{flex:1;height:4px;background:#59636a}
.player-bar .dot{width:12px;height:12px;background:#9aa5ab;border-radius:2px}
.success-btn{position:absolute;left:0;right:0;top:400px;text-align:center}
.success-btn span{display:inline-block;background:var(--teal);color:var(--white);font-weight:700;font-size:16px;padding:12px 34px;border-radius:24px}

/* info */
.info{top:1970px;height:450px;display:flex;padding:10px 40px 0;gap:50px}
.info-main{position:static;width:680px}
.info-main h3{font-size:26px;font-weight:700;line-height:1.3}
.info-main p{font-size:13px;line-height:1.6;margin-top:14px;color:var(--muted)}
.info-main ul{margin:10px 0 0 20px;font-size:13px;line-height:1.7;color:var(--muted)}
.info-note{width:390px}
.info-note h3{font-size:24px;font-weight:600;border-bottom:1px solid #d5dcde;padding-bottom:8px}
.info-note ul{list-style:none;margin-top:12px}
.info-note li{font-size:13px;line-height:1.55;color:var(--muted);padding-left:20px;position:relative;margin-bottom:8px}
.info-note li::before{content:"";position:absolute;left:2px;top:7px;width:8px;height:8px;background:var(--teal);border-radius:50%}

/* footer */
.site-footer{top:2420px;height:340px;background:var(--teal-dark);color:var(--white);display:flex;padding:32px 40px 0;gap:40px}
.f-col{width:250px}
.f-col h4{font-size:22px;font-weight:700;margin-bottom:16px}
.f-col p{font-size:12px;line-height:1.6;color:#d4eaec;margin-bottom:10px}
.newsletter{display:flex;margin-top:14px}
.newsletter span{flex:1;height:34px;background:var(--white);border-radius:18px 0 0 18px;color:#9aa;font-size:12px;padding:9px 14px}
.newsletter b{width:46px;height:34px;background:var(--orange);border-radius:0 18px 18px 0}
.gallery{display:grid;grid-template-columns:repeat(3,70px);gap:8px}
.gallery span{height:60px;background:linear-gradient(135deg,#5fb4bb,#2e858e)}
.bottom-bar{top:2760px;height:80px;background:var(--teal-deep);color:#cfe6e8;text-align:center;font-size:12px;padding-top:20px;line-height:2}
</style>
</head>
<body>

<header class="site-header">
  <div class="promo-pill">Find The Perfect Speaker For The Next Event Here...</div>
  <div class="promo-sub">free industry service</div>
  <div class="promo-tag">Looking for a motivational guest or speakers,<br>MC or industry expert as well as 'WOW' your next event? <b>Find More here.</b></div>
  <div class="social"><span></span><span></span><span></span><span></span></div>
</header>

<nav class="main-nav">
  <a>HOME</a><a>SPEAKERS</a><a>ENTERTAINERS</a><a>TEAM BUILDING</a><a>WELLNESS</a><a>ENQUIRE NOW</a><a>FEATURED SPEAKERS</a><a>CONTACT</a><a>ABOUT</a>
</nav>

<section class="hero">
  <div class="hero-photo" role="img" aria-label="Speaker in a suit presenting with a microphone to a seated audience"></div>
  <span class="hero-arrow" style="left:30px"><svg viewBox="0 0 40 40"><path d="M23 13l-7 7 7 7" fill="none" stroke="#fff" stroke-width="3"/></svg></span>
  <span class="hero-arrow" style="right:30px"><svg viewBox="0 0 40 40"><path d="M17 13l7 7-7 7" fill="none" stroke="#fff" stroke-width="3"/></svg></span>
  <div class="hero-caption">
    <div class="hero-title">PROFESSIONAL SPEAKERS</div>
    <div class="hero-sub">Presenters for the business sector</div>
    <div class="hero-btn">LEARN MORE</div>
  </div>
</section>

<section class="featured">
  <h2>Featured Speakers</h2>
  <div class="carousel-ctrl">
    <span><svg viewBox="0 0 44 44"><path d="M25 15l-7 7 7 7" fill="none" stroke="#fff" stroke-width="3"/></svg></span>
    <span><svg viewBox="0 0 44 44"><path d="M19 15l7 7-7 7" fill="none" stroke="#fff" stroke-width="3"/></svg></span>
  </div>
  <div class="speaker-row">
    <div class="speaker" style="left:0;width:140px" role="img" aria-label="Speaker portrait"></div>
    <div class="speaker" style="left:150px;width:150px" role="img" aria-label="Speaker portrait"></div>
    <div class="speaker" style="left:310px;width:150px" role="img" aria-label="Speaker portrait"></div>
    <div class="speaker-card">
      <div class="photo" role="img" aria-label="Featured speaker portrait"></div>
      <div class="name">Dean Harlow</div>
      <div class="profile">VIEW PROFILE</div>
    </div>
    <div class="speaker" style="left:740px;width:150px" role="img" aria-label="Speaker portrait"></div>
    <div class="speaker" style="left:900px;width:150px" role="img" aria-label="Speaker portrait"></div>
    <div class="speaker" style="left:1060px;width:140px" role="img" aria-label="Speaker portrait"></div>
  </div>
</section>

<section class="welcome">
  <h2>Welcome To Podium Talent Group</h2>
  <p>Podium Talent Group is a free industry service designed to help people looking for speakers and presenters find the most suitable speaker for their needs. Suggestions are given by experienced staff who have presented around Australia for a number of years and know many of our top speakers, presenters and MCs, as well as the leading speaker bureaus across the country.</p>
  <div class="form-btn">Quick Online Custom Form</div>
</section>

<section class="video">
  <div class="player">
    <div class="play"><svg viewBox="0 0 54 54"><path d="M21 16l18 11-18 11z" fill="#fff"/></svg></div>
    <div class="play-label">Click Here To Play</div>
    <div class="player-bar"><span class="dot"></span><span class="track"></span><span class="dot"></span><span class="dot"></span></div>
  </div>
  <div class="success-btn"><span>Click Here To Make Our Event A Great Success</span></div>
</section>

<section class="info">
  <div class="info-main">
    <h3>Are you looking for a Guest or Keynote Speaker - Inspiring, Entertaining, Industry Expert etc. for a conference or special event?</h3>
    <p>Podium Talent Group is a free industry service designed to help people looking for speakers and presenters find the most suitable speaker for their needs. Suggestions are given by experienced staff who have presented around Australia for many years and know many of our top speakers and MCs.</p>
    <p>If you would like a hand finding some great speaker options, simply send us the details of your event and the type of presenter you are looking for.</p>
    <ul>
      <li>Type/topic – Motivational, Overcoming Adversity, Workshop, MC etc</li>
      <li>Type/topic – Team building, Leadership, Inspiration, Health and Business</li>
      <li>Approximate budget – $1000, $3000, $5000, $7000+ etc</li>
      <li>Location – Sydney, Melbourne, Brisbane, Perth, Adelaide, Canberra etc</li>
    </ul>
    <p>... and where we can, we will be happy to send you some speaker possibilities. Custom speakers, bureaus or simply some thoughts on the best choice for you to look into.</p>
  </div>
  <div class="info-note">
    <h3>Please Note:</h3>
    <ul>
      <li>Any information you provide will ONLY ever be used to help with your speaker enquiry.</li>
      <li>More often we have vast and unbiased experience with many speakers, and can suggest options that suit your event and audience well.</li>
      <li>Suggested speakers may come from different agencies and bureaus, so you can compare several options before deciding.</li>
      <li>Please understand that while there is no request too big, a short delay may occur when demand for speakers is high.</li>
    </ul>
  </div>
</section>

<footer class="site-footer">
  <div class="f-col">
    <h4>Podium Talent Group</h4>
    <p>Speakers are not only presenters, they are experts, entertainers and leaders for every kind of event.</p>
    <p>Phone: +61 2 9555 0142<br>Address: 12 Harbour Lane, Sydney NSW 2000<br>Email: hello@podiumtalentgroup.com.au</p>
  </div>
  <div class="f-col">
    <h4>Recent Posts</h4>
    <p>Choosing a keynote that lifts the whole conference room<br>July 23 2015 | 0 comments</p>
    <p>Five questions to ask before booking a master of ceremonies<br>July 23 2015 | 0 comments</p>
  </div>
  <div class="f-col">
    <h4>Newsletter Signup</h4>
    <p>Receive speaker updates and event tips from our team, delivered straight to your inbox each month.</p>
    <div class="newsletter"><span>Email</span><b></b></div>
  </div>
  <div class="f-col">
    <h4>Gallery</h4>
    <div class="gallery" role="img" aria-label="Gallery of event photographs">
      <span></span><span></span><span></span><span></span><span></span><span></span>
    </div>
  </div>
</footer>

<div class="bottom-bar" style="position:absolute;left:0;width:1200px">
  Privacy Policy &nbsp;|&nbsp; ABN 00 000 000 000 &nbsp;|&nbsp; Terms &amp; Conditions<br>
  Copyright © 2015 All Rights Reserved
</div>

</body>
</html>
```